Business card for Luxury Portable Restroom Trailer company

We are a Luxury Portable Restroom Trailer Company Called FALCRIDGE HIRES. Based in Orange County California. We provide portable restroom trailers for events, such as, Weddings, Concerts, Charity events, Sporting events, Tournaments, Corporate events, ect. We rent and Sell the Luxury restrooms. Our colors are white, grey, and Orange. As you will see in the logo we uploaded.
There are 2 people in the company so the names and titles will change for the 3 people but card will remain the same. Here is the information for each Person: Dwight Penner CFO 555 318-0476
next Person: Leon Marchetti VP 555 318-0476
Next Person: Owen Marchetti CEO 555 318-0476
Information to include on the card: Luxury Restroom Trailers Rental and Sales. Weddings, Concerts, Charity, Sporting and Corp. Events.

```html
<!DOCTYPE html>
<html lang="en">
<head>
<meta charset="utf-8">
<title>Falcridge Hires — Business Card</title>
<link rel="stylesheet" href="https://fonts.googleapis.com/css2?family=Montserrat:wght@400;500;700;800&display=swap">
<style>
  :root {
    --bg: #1b1b1b;
    --card: #232323;
    --card-deep: #1e1e1e;
    --orange: #f26b1d;
    --white: #f4f4f4;
    --grey: #b9b9b9;
    --pattern-a: #2c2c2c;
    --pattern-b: #3a3a3a;
  }
  * { box-sizing: border-box; margin: 0; padding: 0; }
  html, body { width: 1200px; height: 801px; overflow: hidden; }
  body {
    background: var(--bg);
    font-family: "Montserrat", Arial, sans-serif;
    display: flex;
    align-items: center;
    justify-content: center;
    gap: 40px;
  }
  .card {
    position: relative;
    width: 540px;
    height: 309px;
    background: var(--card);
    border-bottom: 3px solid var(--orange);
    border-left: 2px solid var(--orange);
    box-shadow: 0 18px 40px rgba(0,0,0,.55);
    overflow: hidden;
  }
  /* front */
  .brand {
    position: absolute;
    left: 60px; top: 46px;
    display: flex; align-items: center; gap: 12px;
  }
  .brand-square {
    width: 30px; height: 30px;
    border: 3px solid var(--orange);
  }
  .brand-name {
    font-weight: 800;
    font-size: 30px;
    letter-spacing: 1px;
    color: var(--white);
    line-height: 1;
  }
  .person {
    position: absolute;
    left: 60px; top: 140px;
    width: 220px;
    text-align: right;
  }
  .person-name {
    font-weight: 700;
    font-size: 20px;
    color: var(--orange);
    letter-spacing: .5px;
    white-space: nowrap;
  }
  .person-title {
    font-weight: 400;
    font-size: 13px;
    color: var(--white);
    margin-top: 2px;
  }
  .divider {
    position: absolute;
    left: 296px; top: 128px;
    width: 1px; height: 80px;
    background: var(--orange);
  }
  .contacts {
    position: absolute;
    left: 312px; top: 132px;
    list-style: none;
  }
  .contacts li {
    display: flex; align-items: center; gap: 7px;
    font-size: 12px;
    color: var(--white);
    height: 24px;
  }
  .contacts svg { width: 11px; height: 11px; fill: var(--orange); flex: none; }
  .tagline {
    position: absolute;
    left: 60px; bottom: 36px;
  }
  .tagline-main {
    font-weight: 500;
    font-size: 15px;
    color: var(--orange);
  }
  .tagline-events {
    font-weight: 400;
    font-size: 15px;
    color: var(--white);
    margin-top: 6px;
  }
  /* back */
  .back-pattern {
    position: absolute; inset: 0;
    background: linear-gradient(120deg, var(--card-deep) 0%, var(--pattern-a) 45%, var(--pattern-b) 100%);
  }
  .back-badge {
    position: absolute;
    right: 56px; top: 152px;
    display: flex; align-items: center; gap: 10px;
  }
  .back-badge-circle {
    width: 44px; height: 44px;
    border-radius: 50%;
    border: 4px solid var(--orange);
  }
  .back-badge-name {
    font-weight: 700;
    font-size: 14px;
    color: var(--orange);
    letter-spacing: .5px;
  }
</style>
</head>
<body>

<section class="card card-front">
  <div class="brand">
    <span class="brand-square"></span>
    <span class="brand-name">FALCRIDGE HIRES</span>
  </div>

  <div class="person">
    <p class="person-name">OWEN MARCHETTI</p>
    <p class="person-title">CEO</p>
  </div>

  <span class="divider"></span>

  <ul class="contacts">
    <li>
      <svg viewBox="0 0 24 24"><path d="M6.6 10.8a15.1 15.1 0 0 0 6.6 6.6l2.2-2.2a1 1 0 0 1 1-.25 11.4 11.4 0 0 0 3.6.57 1 1 0 0 1 1 1V20a1 1 0 0 1-1 1A17 17 0 0 1 3 4a1 1 0 0 1 1-1h3.5a1 1 0 0 1 1 1c0 1.25.2 2.45.57 3.6a1 1 0 0 1-.25 1z"/></svg>
      555 318-0476
    </li>
    <li>
      <svg viewBox="0 0 24 24"><path d="M2 5h20v14H2zm2 2v.5l8 5 8-5V7z"/></svg>
      owen@falcridgehires.com
    </li>
    <li>
      <svg viewBox="0 0 24 24"><circle cx="12" cy="12" r="10"/></svg>
      www.falcridgehires.com
    </li>
  </ul>

  <div class="tagline">
    <p class="tagline-main">Luxury Restroom Trailers Rental and Sales</p>
    <p class="tagline-events">Weddings | Concerts | Charity | Sporting | Corp</p>
  </div>
</section>

<section class="card card-back">
  <div class="back-pattern" role="img" aria-label="Repeating pattern of the company emblem in glossy dark grey circles"></div>
  <div class="back-badge">
    <span class="back-badge-circle"></span>
    <span class="back-badge-name">FALCRIDGE HIRES</span>
  </div>
</section>

</body>
</html>
```